Designing a Mailer/Courier bag with our Company Logo for Product Shipping

We need a quirky Mailer/Courier Bag for our company, Renard Céleste. As a luxury French, vintage-inspired fashion brand, we take pride in the presentation of our products, and we believe that a stylish and branded packing satchel will enhance our customers' experience.

We are looking for a design that incorporates our company logo, ‘Renard Céleste’ while being very feminine and French-inspired. The satchel should be practical, with a section (10.4cm x 16.5cm) for the shipping label to be placed onto the bag without it covering any logos. We are open to different colours, and designs, as long as they align with our brand image.

The packing satchel will be used to ship our products to customers worldwide, so we need a versatile design that can accommodate different-sized packing satchels.

To gain further inspiration on what type of brand Renard Céleste is please visit our website https://renardceleste.example/.

Some ideas I have attached in the images below:
- Quirky
- Looks like old mail
- Has a feel-good written phrase on the back of the packaging
- Looks vintage and unique

```html
<!DOCTYPE html>
<html lang="en">
<head>
<meta charset="utf-8">
<title>Renard Céleste – Mailer Bag Colourways</title>
<link href="https://fonts.googleapis.com/css2?family=Cinzel:wght@700;900&display=swap" rel="stylesheet">
<style>
  :root {
    --page: #ffffff;
    --ink: #1e1a17;
    --ink-light: #f1ece4;
    --teal: #3bb1b7;
    --teal-soft: #9fd6d9;
    --label: #ffffff;

    --ochre-a: #e6b35f; --ochre-b: #d6981f; --ochre-line: #c56b1e;
    --sand-a: #efd9aa;  --sand-b: #d9b451;  --sand-line: #c9a164;
    --aqua-a: #d6eff1;  --aqua-b: #a3d9de;  --aqua-line: #86ccd2;
    --kraft-a: #ad6e33; --kraft-b: #8b5114; --kraft-line: #4f2a0e;
    --linen-a: #eee7d8; --linen-b: #d6cca9; --linen-line: #c6b994;
  }
  * { margin: 0; padding: 0; box-sizing: border-box; }
  html, body { width: 1200px; height: 1108px; overflow: hidden; background: var(--page); }
  body { position: relative; font-family: "Cinzel", Georgia, serif; }

  .mailer {
    position: absolute;
    width: 332px;
    height: 457px;
    background: linear-gradient(100deg, var(--a) 0%, var(--a) 55%, var(--b) 100%);
  }
  .mailer__frame {
    position: absolute;
    inset: 8px;
    border: 1.5px solid var(--line);
  }
  .mailer__fold {
    position: absolute;
    top: 0; bottom: 0;
    left: 278px;
    width: 1px;
    background: rgba(0,0,0,0.08);
  }
  .mailer__brand {
    position: absolute;
    left: 0; right: 0;
    top: 48px;
    text-align: center;
    font-weight: 900;
    font-size: 29px;
    letter-spacing: 0.5px;
    color: var(--ink);
  }
  .mailer--kraft .mailer__brand { color: var(--ink-light); top: 40px; }

  .label {
    position: absolute;
    width: 90px;
    height: 137px;
    background: var(--label);
    border: 4px dotted var(--teal);
    border-radius: 4px;
    box-shadow: 0 0 0 1px var(--teal-soft);
  }
  .label--small { width: 80px; height: 121px; }
  .label__to {
    position: absolute;
    top: 8px; left: 8px;
    font-weight: 700;
    font-size: 11px;
    color: var(--teal);
  }

  .mailer--ochre { left: 67px;  top: 83px;  --a: var(--ochre-a); --b: var(--ochre-b); --line: var(--ochre-line); }
  .mailer--sand  { left: 433px; top: 88px;  --a: var(--sand-a);  --b: var(--sand-b);  --line: var(--sand-line); }
  .mailer--aqua  { left: 788px; top: 90px;  --a: var(--aqua-a);  --b: var(--aqua-b);  --line: var(--aqua-line); }
  .mailer--kraft { left: 68px;  top: 573px; --a: var(--kraft-a); --b: var(--kraft-b); --line: var(--kraft-line); }
  .mailer--linen { left: 433px; top: 575px; --a: var(--linen-a); --b: var(--linen-b); --line: var(--linen-line); }

  .quantity {
    position: absolute;
    right: 22px;
    bottom: 16px;
    font-family: Arial, Helvetica, sans-serif;
    font-size: 10px;
    color: #222;
  }
</style>
</head>
<body>
  <section class="mailer mailer--ochre">
    <div class="mailer__frame"></div>
    <div class="mailer__fold"></div>
    <p class="mailer__brand">Renard Céleste</p>
    <div class="label" style="left:33px; top:143px;"><span class="label__to">TO</span></div>
  </section>

  <section class="mailer mailer--sand">
    <div class="mailer__frame"></div>
    <div class="mailer__fold"></div>
    <p class="mailer__brand">Renard Céleste</p>
    <div class="label" style="left:37px; top:116px;"><span class="label__to">TO</span></div>
  </section>

  <section class="mailer mailer--aqua">
    <div class="mailer__frame"></div>
    <div class="mailer__fold"></div>
    <p class="mailer__brand">Renard Céleste</p>
    <div class="label" style="left:38px; top:115px;"><span class="label__to">TO</span></div>
  </section>

  <section class="mailer mailer--kraft">
    <div class="mailer__frame"></div>
    <div class="mailer__fold"></div>
    <p class="mailer__brand">Renard Céleste</p>
    <div class="label label--small" style="left:32px; top:102px;"><span class="label__to">TO</span></div>
  </section>

  <section class="mailer mailer--linen">
    <div class="mailer__frame"></div>
    <div class="mailer__fold"></div>
    <p class="mailer__brand">Renard Céleste</p>
    <div class="label label--small" style="left:32px; top:102px;"><span class="label__to">TO</span></div>
  </section>

  <p class="quantity">X14</p>
</body>
</html>
```